Unternehmensbroschüre
Zielgruppe
Unternehmen
Aufgabenstellung
Gestalten Sie aus dem gelieferten Text eine exklusive 12-seitige Unternehmensbroschüre im Premium-Stil. Die Broschüre richtet sich an Geschäftsführer und HR-Verantwortliche von Schweizer KMU. Sie soll sich nicht wie Werbung, sondern wie ein hochwertiges Markenmagazin oder Manifest lesen.
Designvorgaben:
Minimalistisch, elegant und zeitlos.
Viel Weissraum.
Grosse, starke Typografie.
Ruhiges Schweizer Design (Quern, Vostra, Malvent, Ordevina als Inspiration).
Keine überladenen Layouts.
Keine typischen Business-Stockfotos.
Maximal 3–4 emotionale Bilder in der gesamten Broschüre.
Wo möglich, mit grafischen Elementen statt Fotos arbeiten.
Jede Doppelseite soll einen eigenen Rhythmus und Charakter haben.
Farben: Weiss, Anthrazit, Türkis als Akzent, Gold sehr sparsam.
Das KoruMed-Logo und die Markenidentität sollen dezent und hochwertig integriert werden.
Ziel: Der Geschäftsführer soll die Broschüre nicht nur lesen, sondern bis zur letzten Seite in der Hand behalten und das Gefühl haben, Teil einer neuen Gesundheitsbewegung werden zu können.

```html
<!DOCTYPE html>
<html lang="de">
<head>
<meta charset="utf-8">
<title>KoruMed – Pilotprogramm 2026</title>
<link href="https://fonts.googleapis.com/css2?family=Cinzel:wght@400;500;600&family=Poppins:ital,wght@0,400;0,500;0,600;0,700;1,600&display=swap" rel="stylesheet">
<style>
:root{
  --teal:#17878a;
  --teal-dark:#0f6f72;
  --teal-soft:#d3e9e7;
  --gold:#b68a22;
  --gold-soft:#d4a83c;
  --ink:#333638;
  --muted:#5d6163;
  --paper:#ffffff;
  --stage:#c4c4c4;
}
*{box-sizing:border-box;margin:0;padding:0}
html,body{width:1200px;height:3000px;overflow:hidden;background:var(--stage)}
body{position:relative;font-family:"Poppins",sans-serif;color:var(--ink)}
.serif{font-family:"Cinzel",serif}
.page{position:absolute;width:500px;height:700px;background:var(--paper);overflow:hidden}
.spread{position:absolute;left:100px;width:1000px;height:700px}
.spread .left{left:0;box-shadow:inset -14px 0 18px -14px rgba(0,0,0,.18)}
.spread .right{left:500px;box-shadow:inset 14px 0 18px -14px rgba(0,0,0,.18)}
.abs{position:absolute}
.ph{position:absolute}
.teal{color:var(--teal)} .gold{color:var(--gold)}
.box{position:absolute;background:var(--teal-soft);border-radius:10px}
.small{font-size:8.5px;line-height:1.55;color:var(--muted)}
.lead{font-weight:600;color:var(--teal);font-size:11px;line-height:1.3}
.goldhead{font-weight:600;color:var(--gold);font-size:11px;line-height:1.3}
ul.dots{list-style:none}
ul.dots li{position:relative;padding-left:12px}
ul.dots li::before{content:"";position:absolute;left:0;top:.55em;width:4px;height:4px;border-radius:50%;background:var(--gold)}

/* cover */
.cover{left:350px;top:30px}
.cover .landscape{left:0;top:0;width:500px;height:340px;background:linear-gradient(180deg,#e7c98a 0%,#d59a3a 35%,#c8a25a 60%,#e9d7b0 85%,#ffffff 100%)}
.brand{position:absolute;left:150px;top:40px;display:flex;align-items:center;gap:8px;background:rgba(255,255,255,.85);padding:6px 14px;border-radius:4px}
.brand .dot{width:18px;height:18px;border-radius:50%;background:var(--teal)}
.brand span{font-weight:700;font-size:20px;color:var(--teal-dark);letter-spacing:.5px}
.cover h2{position:absolute;left:50px;top:360px;font-size:19px;font-weight:600;color:var(--gold);letter-spacing:1px}
.cover h1{position:absolute;left:50px;top:388px;font-size:44px;line-height:1.02;font-weight:500;color:var(--teal)}
.cover .intro{position:absolute;left:50px;top:500px;width:380px;font-size:11.5px;font-weight:600;line-height:1.45;color:var(--ink)}
.cover .pilot{position:absolute;left:50px;top:560px;color:var(--teal);font-weight:600;font-size:14px}
.cover .year{position:absolute;left:50px;top:576px;color:var(--teal);font-weight:700;font-size:44px;line-height:1}
.cover .target{position:absolute;left:250px;top:572px;width:200px;font-size:9px;line-height:1.45;color:var(--muted)}
.cover .foot{position:absolute;left:50px;top:640px;display:flex;align-items:center;gap:14px}
.cover .foot .name{font-family:"Cinzel",serif;font-size:20px;color:var(--teal)}
.cover .foot .bar{width:2px;height:30px;background:var(--gold)}
.cover .foot .claim{font-size:9.5px;color:var(--gold)}

/* spread 1 */
.s1{top:780px}
.burn{position:absolute;left:0;width:500px;top:55px;text-align:center;color:var(--teal)}
.burn .big{font-size:46px;line-height:1;font-weight:500}
.burn .statt{display:flex;align-items:center;justify-content:center;gap:10px;font-size:16px;letter-spacing:6px;margin:6px 0}
.burn .statt i{display:block;width:70px;height:1px;background:var(--teal)}
.burn .big .g{color:var(--gold)}
.s1 .facts{left:40px;top:215px;width:210px}
.s1 .facts .item{margin-bottom:14px}
.s1 .facts .item p{margin-top:4px}
.s1 .folgen{left:275px;top:205px;width:190px;height:170px;padding:14px 16px}
.s1 .folgen h4{font-size:11px;color:var(--teal);font-weight:600;margin-bottom:8px;text-align:center}
.s1 .folgen li{font-size:9px;font-weight:600;color:var(--ink);margin-bottom:6px}
.s1 .steps{left:40px;top:400px;width:200px}
.s1 .steps p{margin-bottom:12px}
.s1 .figure{left:220px;top:410px;width:140px;height:190px;background:linear-gradient(160deg,#eef6f6,#d8ecea)}
.s1 .badge{left:360px;top:420px;width:115px;height:115px;border-radius:50%;background:radial-gradient(circle at 35% 30%,#d6a93d,#a67915);color:#fff;display:flex;align-items:center;justify-content:center;text-align:center;font-family:"Cinzel",serif;font-size:8.5px;line-height:1.3;padding:16px}
.s1 .footline{left:40px;top:650px;font-size:8.5px;color:var(--muted)}
.s1 .clock{left:0;top:30px;width:120px;height:150px}
.s1 .rhead{position:absolute;left:0;width:500px;text-align:center}
.s1 .r1{top:50px;font-family:"Cinzel",serif;color:var(--gold);font-size:17px;line-height:1.2}
.s1 .r2{top:105px;font-size:10px;font-weight:600;color:var(--teal)}
.s1 .r3{top:122px;font-size:8.5px;color:var(--muted);line-height:1.5}
.s1 .ihre{font-family:"Cinzel",serif;color:var(--gold);font-size:12px;letter-spacing:2px}
.s1 .huge{font-family:"Cinzel",serif;color:var(--teal);font-size:40px;line-height:1.05;font-weight:500}
.s1 .r4{top:175px}
.s1 .r5{top:310px;font-size:8.5px;line-height:1.55;color:var(--muted)}
.s1 .r5 b{color:var(--gold);font-weight:600}
.s1 .pill{left:115px;top:355px;width:270px;height:24px;border-radius:12px;background:var(--gold);color:#fff;font-size:8.5px;font-weight:600;display:flex;align-items:center;justify-content:center}
.s1 .pillars{left:20px;top:410px;width:460px;height:155px;display:flex;justify-content:space-around;padding:14px 10px}
.pillar{width:130px;text-align:center}
.pillar .ic{width:30px;height:30px;border-radius:50%;background:var(--teal);margin:0 auto 8px;display:flex;align-items:center;justify-content:center}
.pillar h5{font-size:10px;color:var(--teal);font-weight:600;line-height:1.25;margin-bottom:6px}
.pillar p{font-size:8px;line-height:1.5;color:var(--muted)}
.s1 .r6{top:580px;font-size:9px;font-style:italic;font-weight:600;color:var(--gold);line-height:1.5}

/* spread 2 */
.s2{top:1530px}
.s2 .title{left:0;width:500px;top:55px;text-align:center;font-family:"Cinzel",serif;font-size:40px;line-height:1.05;color:var(--teal);font-weight:500}
.s2 .claim{left:40px;top:215px;width:200px}
.s2 .claim p.small{margin-top:8px}
.s2 .photo{left:0;top:380px;width:500px;height:260px;background:linear-gradient(180deg,#e6b86a 0%,#c9853a 45%,#7a5a3a 80%,#4e3e2e 100%)}
.s2 .sol{left:275px;top:200px;width:195px;height:420px;padding:14px 16px;font-size:8.5px;line-height:1.6;font-weight:600}
.s2 .sol .t{color:var(--teal)}
.s2 .sol .d{color:var(--ink)}
.s2 .sol .gap{height:10px}
.s2 .band{left:0;top:640px;width:500px;height:60px;background:var(--gold);color:#fff;font-size:9px;font-style:italic;font-weight:600;display:flex;align-items:center;justify-content:center;text-align:center;padding:0 40px;line-height:1.5}
.s2 .rt{left:0;width:500px;text-align:center;font-family:"Cinzel",serif}
.s2 .rt1{top:50px;color:var(--gold);font-size:15px}
.s2 .rt2{top:72px;color:var(--teal);font-size:40px;line-height:1.05;font-weight:500}
.s2 .rule{top:125px;height:1px;background:var(--teal);width:70px}
.s2 .col1{left:50px;top:170px;width:200px;font-size:8.5px;line-height:1.4;color:var(--muted)}
.s2 .col1 p{margin-bottom:8px}
.s2 .col2{left:295px;top:170px;width:170px;font-size:8.5px;color:var(--muted)}
.s2 .col2 h4{font-size:13px;font-weight:600;color:var(--teal);line-height:1.2;margin-bottom:10px}
.s2 .col2 p{margin-bottom:8px}
.s2 .meeting{left:40px;top:420px;width:420px;height:170px;background:linear-gradient(180deg,#f1f8f8,#ddeeed)}
.s2 .ask{left:0;width:500px;top:610px;text-align:center;font-family:"Cinzel",serif;color:var(--gold);font-size:15px;line-height:1.3}

/* spread 3 */
.s3{top:2280px}
.s3 .kick{left:60px;top:60px;font-family:"Cinzel",serif;color:var(--gold);font-size:15px}
.s3 .now{left:50px;top:90px;font-family:"Cinzel",serif;color:var(--teal);line-height:1.05}
.s3 .now .b{font-size:44px;font-weight:500}
.s3 .now .s{font-size:18px}
.s3 .win{left:50px;width:200px}
.s3 .win .h{display:flex;align-items:center;gap:8px;font-weight:600;color:var(--gold);font-size:11px;margin-bottom:4px}
.s3 .win .h i{width:20px;height:20px;border-radius:50%;background:var(--gold-soft)}
.s3 .win ul{font-size:8.5px;color:var(--muted);line-height:1.6;margin-left:28px}
.s3 .trophy{left:250px;top:230px;width:200px;height:350px;background:linear-gradient(180deg,#f1f8f8,#d9ecea)}
.s3 .sign{left:50px;top:600px;display:flex;align-items:center;gap:18px}
.s3 .sign .n{font-weight:600;color:var(--gold);font-size:16px}
.s3 .sign .t{font-size:8px;color:var(--muted);width:230px;line-height:1.5}
.s3 .band{left:0;top:650px;width:500px;height:50px;background:var(--teal-soft);display:flex;align-items:center;justify-content:center;font-size:10px;font-weight:600;color:var(--ink)}
.s3 .rt{left:0;width:500px;top:45px;text-align:center;font-family:"Cinzel",serif;font-size:38px;line-height:1.02;color:var(--teal);font-weight:500}
.s3 .rt .g{color:var(--gold)}
.s3 .rtext{left:40px;top:200px;width:180px;font-size:8.5px;line-height:1.45;color:var(--muted)}
.s3 .rtext p{margin-bottom:10px}
.s3 .inv{left:255px;top:185px;width:210px;height:235px;padding:12px 16px}
.s3 .inv h4{text-align:center;font-size:10px;color:var(--gold);font-weight:600;margin-bottom:10px}
.s3 .inv .row{margin-bottom:12px}
.s3 .inv .row .h{display:flex;align-items:center;gap:8px;font-size:8.5px;font-weight:600;color:var(--teal);margin-bottom:4px}
.s3 .inv .row .h i{width:18px;height:18px;border-radius:50%;background:var(--teal);flex:none}
.s3 .inv .row p{font-size:8px;line-height:1.5;color:var(--ink)}
.s3 .crowd{left:0;top:430px;width:500px;height:270px;background:linear-gradient(180deg,#f4ead6 0%,#d9a45a 35%,#b5713a 70%,#7c5a3c 100%)}
</style>
</head>
<body>

<!-- Cover -->
<section class="page cover">
  <div class="ph landscape" role="img" aria-label="Aquarell einer goldenen Herbstlandschaft mit Flusslauf und Tannen"></div>
  <div class="brand"><i class="dot"></i><span>VELTARA</span></div>
  <h2 class="serif">GESUNDE MITARBEITENDE</h2>
  <h1 class="serif">BRAUCHEN<br>ORIENTIERUNG</h1>
  <p class="intro">Manchmal braucht Gesundheit nicht noch mehr Methoden. Sondern eine neue Richtung. Gemeinsam mit Unternehmen geht KoruMed diesen Weg.</p>
  <p class="pilot">Pilotprogramm</p>
  <p class="year">2026</p>
  <p class="target">Für Unternehmen, die Betriebliches Gesundheits&shy;management neu denken.</p>
  <div class="foot"><span class="name">KORUMED</span><i class="bar"></i><span class="claim">Der Verein für eine solidarische Gesundheitsversorgung.</span></div>
</section>

<!-- Spread 1 -->
<section class="spread s1">
  <div class="page left">
    <div class="burn serif">
      <div class="big">BURN-IN</div>
      <div class="statt"><i></i>STATT<i></i></div>
      <div class="big">BURN-<span class="g">OUT</span></div>
    </div>
    <div class="abs facts">
      <div class="item"><p class="lead">Überforderung ist kein Gefühl. Sie ist ein Kostenfaktor.</p><p class="small">Ein modernes Unternehmen muss in Digitalisierung, Prozesse und Wachstum investieren.</p></div>
      <div class="item"><p class="lead">Doch High-Tech funktioniert nur mit High-Human.</p><p class="small">Fehlt Orientierung, wird aus Belastung Überforderung. Aus Motivation wird Erschöpfung. Aus Leistung werden Fehlzeiten.</p></div>
    </div>
    <div class="box folgen">
      <h4>Die Folgen.</h4>
      <ul class="dots">
        <li>Steigende Absenzen</li><li>Innere Kündigung</li><li>Fachkräftemangel</li><li>Sinkende Motivation</li><li>Höhere Fluktuation</li><li>Steigende Gesundheitskosten</li>
      </ul>
    </div>
    <div class="abs steps">
      <p class="goldhead">Deshalb braucht Gesundheit einen neuen Blick.</p>
      <p class="goldhead">Nicht Einzelmassnahmen. Kontinuität.</p>
      <p class="goldhead">Kontinuität schafft Vertrauen.</p>
      <p class="goldhead">Vertrauen schafft Veränderung.</p>
    </div>
    <div class="ph figure" role="img" aria-label="Linienzeichnung einer springenden Person"></div>
    <div class="abs badge">Burn-out beginnt nicht an einem einzigen Tag. Gesundheit aber auch nicht.</div>
    <p class="abs footline">Getragen von einer Gemeinschaft, die Gesundheit lebbar macht, bevor Krankheit entsteht.</p>
  </div>
  <div class="page right">
    <div class="ph clock" role="img" aria-label="Linienzeichnung einer Uhr"></div>
    <p class="rhead r1">ZEIT IST DIE NEUE WÄHRUNG<br>DER WERTSCHÄTZUNG.</p>
    <p class="rhead r2">Gesundheitszeit statt Ausfallzeit.</p>
    <p class="rhead r3">Mitarbeitende schenken Ihrem Unternehmen jeden Tag<br>das Wertvollste, das sie besitzen</p>
    <div class="rhead r4">
      <div class="ihre">IHRE</div>
      <div class="huge">LEBENSZEIT.</div>
      <div class="ihre">IHRE</div>
      <div class="huge">ENERGIE.</div>
    </div>
    <p class="rhead r5">Wer heute Höchstleistung erwartet, muss <b>zuerst Energie zurückgeben.</b><br>Wenn Sie Ihrem Team gezielt Gesundheitszeit ermöglichen, verändern Sie mehr als<br>Gesundheit. Sie investieren nicht in ein BGM-Konzept.</p>
    <div class="abs pill">Sie investieren in das Herz Ihrer Firma: den Menschen.</div>
    <div class="box pillars">
      <div class="pillar">
        <div class="ic"><svg width="14" height="16" viewBox="0 0 14 16"><circle cx="7" cy="3" r="2.4" fill="#fff"/><path d="M3 7h8v3H9v6H5v-6H3z" fill="#fff"/></svg></div>
        <h5>Menschlichkeit<br>erleben</h5><p>Wer sich als Mensch geschätzt fühlt, arbeitet nicht mehr nur für den Lohn.</p>
      </div>
      <div class="pillar">
        <div class="ic"><svg width="14" height="16" viewBox="0 0 14 16"><circle cx="7" cy="6" r="4.5" fill="none" stroke="#fff" stroke-width="1.6"/><path d="M4 10l-1 5 4-2 4 2-1-5" fill="#fff"/></svg></div>
        <h5>Loyalität<br>verankern</h5><p>Treue lässt sich nicht kaufen. Menschen vergessen nie, wer ihre Gesundheit schützt.</p>
      </div>
      <div class="pillar">
        <div class="ic"><svg width="14" height="16" viewBox="0 0 14 16"><path d="M7 16V6" stroke="#fff" stroke-width="1.6"/><path d="M7 8C3 8 2 5 2 3c3 0 5 2 5 5zM7 6c0-3 2-5 5-5 0 2-1 5-5 5z" fill="#fff"/></svg></div>
        <h5>Gesund<br>wachsen</h5><p>Unternehmen wachsen nicht durch Druck. Sie wachsen durch Menschen, die mit voller Kraft hinter ihnen stehen.</p>
      </div>
    </div>
    <p class="rhead r6">KoruMed verwandelt Ausfallzeit in Gesundheitszeit. Und Gesundheitszeit<br>in gelebte Wertschätzung.</p>
  </div>
</section>

<!-- Spread 2 -->
<section class="spread s2">
  <div class="page left">
    <h2 class="abs title">WARUM EIN<br>VEREIN STATT<br>EINER <span class="gold">FIRMA?</span></h2>
    <div class="abs claim">
      <p class="lead">Gesundheit ist keine Frage des Profits. Sondern der Solidarität.</p>
      <p class="small">KoruMed geht einen neuen Weg.<br>Als Verein verzichten wir bewusst auf Gewinnmaximierung.<br>Unser Ziel ist menschlicher.<br>Wir schaffen eine Gesundheitsgemeinschaft, die verbindet.<br>Verantwortung teilt.<br>Und Gesundheit für alle zugänglich macht.</p>
    </div>
    <div class="ph photo" role="img" aria-label="Gemälde eines Wanderers, der auf einem Felsen in den Sonnenuntergang über den Bergen blickt"></div>
    <div class="box sol">
      <p class="t">Solidarität öffnet Türen.</p>
      <p class="t">Mitarbeitende.<br>Unternehmen.<br>Navigatoren.<br>Gönner.<br>Partner.</p>
      <p class="d">Alle bewirken etwas.<br>Alle tragen Verantwortung.</p>
      <p class="t">Alle gewinnen.</p>
      <div class="gap"></div>
      <p class="t">Der Solidaritätsfonds.</p>
      <p class="d">Jede Mitgliedschaft.<br>Jede Behandlung.<br>Jeder Unternehmensbeitrag.<br>Jeder Beitrag stärkt das gemeinsame Fundament.<br>So entstehen echte Gesundheitschancen.<br>Gerade dort, wo Prävention für alle erreichbar sein soll.</p>
    </div>
    <div class="abs band">Nicht jeder kann gleich viel geben. Aber jeder Beitrag hilft mit, Gesundheit für mehr Menschen Wirklichkeit werden zu lassen.</div>
  </div>
  <div class="page right">
    <p class="abs rt rt1">DAS ERSTE UNTERNEHMEN</p>
    <p class="abs rt rt2">VERÄNDERT<br>ALLES.</p>
    <i class="abs rule" style="left:70px"></i>
    <i class="abs rule" style="left:360px"></i>
    <div class="abs col1">
      <p>Es braucht keine hundert Unternehmen.</p><p>Nicht fünfzig.</p><p>Nicht zehn.</p><p>Es braucht genau eines.</p>
      <p>Eines, das den Mut hat, Gesundheit radikal neu zu denken.</p>
      <p>Eines, das Menschen mehr schenken will als nur einen Lohn.</p>
      <p>Eines, das Verantwortung nicht delegiert, sondern im Alltag lebt.</p>
    </div>
    <div class="abs col2">
      <h4>Das Pionier-<br>Unternehmen</h4>
      <p>Sie gehören zu den Ersten.</p><p>Sie gestalten das Fundament mit.</p><p>Sie setzen ein unübersehbares Zeichen.</p>
      <p>Für Ihr Team.</p><p>Für Ihre Region.</p><p>Für eine neue Kultur der Wertschätzung.</p>
    </div>
    <div class="ph meeting" role="img" aria-label="Linienzeichnung von drei Personen im Gespräch an einem Tisch"></div>
    <p class="abs ask">WERDEN SIE DIESES<br>EINE PIONIER-UNTERNEHMEN?</p>
  </div>
</section>

<!-- Spread 3 -->
<section class="spread s3">
  <div class="page left">
    <p class="abs kick">EIN BEITRAG. VIER GEWINNER.</p>
    <div class="abs now"><span class="b">NICHT</span> <span class="s">IRGENDWANN.</span><br><span class="s">SONDERN</span> <span class="b">HEUTE.</span></div>
    <div class="abs win" style="top:250px"><div class="h"><i></i>Ihr Team</div><ul class="dots"><li>Gewinnt Gesundheit.</li><li>Wertvolle Zeit.</li><li>Klare Orientierung.</li></ul></div>
    <div class="abs win" style="top:360px"><div class="h"><i></i>Ihre Region</div><ul class="dots"><li>Gewinnt ein starkes Gesundheitsnetzwerk.</li><li>Gelebte Solidarität.</li><li>Mehr Zusammenhalt.</li></ul></div>
    <div class="abs win" style="top:470px"><div class="h"><i></i>Ihr Unternehmen</div><ul class="dots"><li>gewinnt echte Motivation.</li><li>Tiefe Verbundenheit.</li><li>Höchste Arbeitgeberattraktivität.</li></ul></div>
    <div class="ph trophy" role="img" aria-label="Linienzeichnung eines Mannes, der einen Pokal hochhält"></div>
    <div class="abs sign"><span class="n">KoruMed</span><span class="t">gewinnt die Möglichkeit, hochwertige Prävention genau dort zugänglich zu machen, wo der Zugang heute oft eine Hürde ist.</span></div>
    <div class="abs band">Ein Beitrag · Vier Gewinner · Eine gemeinsame Zukunft.</div>
  </div>
  <div class="page right">
    <h2 class="abs rt">GESUNDHEIT<br>DARF SICH<br><span class="g">RECHNEN.</span></h2>
    <div class="abs rtext">
      <p>Wirtschaftlicher Erfolg ist keine Frage von Excel-Tabellen.</p>
      <p>Sondern von Menschen mit Energie.</p>
      <p>Präsenz allein bewegt kein Unternehmen.</p>
      <p>Es ist die Energie der Menschen, die den Unterschied macht.</p>
      <p>KoruMed ist deshalb kein Kostenfaktor, sondern ein wichtiges</p>
      <p>Investment in die wichtigste Struktur des Unternehmens. Den Menschen.</p>
    </div>
    <div class="box inv">
      <h4>Sie investieren</h4>
      <div class="row"><div class="h"><i></i>In Performance-Sicherheit</div><p>Mentaler Fokus. Mehr Energie.<br>Mehr Leichtigkeit am Arbeitsplatz.</p></div>
      <div class="row"><div class="h"><i></i>In Kultur-Anker</div><p>Ein Umfeld, das Gesundheit stärkt, Vertrauen schafft und Fachkräfte langfristig bindet.</p></div>
      <div class="row"><div class="h"><i></i>In steueroptimierte Wertschätzung</div><p>Ein echter Mehrwert für Ihre Mitarbeitenden.<br>Nachhaltig für Ihr Unternehmen.</p></div>
    </div>
    <div class="ph crowd" role="img" aria-label="Gemälde einer Gemeinschaft verschiedener Generationen, die sich im Kreis an den Händen hält"></div>
  </div>
</section>

</body>
</html>
```